Meadowlark Property Review is a leading provider of residential appraisal and home inspection products in S

I need a business card/logo designed that obviously describes my business. We are a residential appraisal and home inspection company in Springfield, MO. We offer residential appraisals, home inspection, pest inspection and radon gas measurement. We have been in business for 18 years and hold state certified residential appraisal licenses and OBREX certified home inspection licenses. I have a logo that I really like and will attach, but would be open to new suggestions. I like more modern designs than traditional and would like a two sided card with our services, licenses and qualifications on the back.

```html
<!DOCTYPE html>
<html lang="en">
<head>
<meta charset="utf-8">
<title>Meadowlark Property Review – Business Card</title>
<link href="https://fonts.googleapis.com/css2?family=Source+Sans+3:ital,wght@0,400;0,600;1,400&display=swap" rel="stylesheet">
<style>
  :root {
    --backdrop: #3b3b3b;
    --card-white: #f7f7f7;
    --brown: #8c6d45;
    --orange: #f0851a;
    --ink: #4a4a4a;
    --rule: #9a9a9a;
    --cream: #ffffff;
  }
  * { box-sizing: border-box; margin: 0; padding: 0; }
  html, body {
    width: 1200px; height: 750px; overflow: hidden;
    background: var(--backdrop);
    font-family: "Source Sans 3", sans-serif;
  }
  .stage { position: relative; width: 1200px; height: 750px; }
  .card {
    position: absolute; top: 228px;
    width: 461px; height: 263px;
  }
  .card--front { left: 124px; background: var(--card-white); }
  .card--back { left: 618px; background: var(--brown); }

  .brand-tab {
    position: absolute; left: 75px; top: 0;
    width: 89px; height: 58px; background: var(--brown);
  }
  .brand {
    position: absolute; left: 30px; top: 74px;
    display: flex; align-items: center; gap: 8px;
  }
  .brand__square { width: 12px; height: 12px; background: var(--orange); }
  .brand__name {
    font-weight: 600; font-size: 20px; color: var(--brown);
    letter-spacing: 0.2px;
  }

  .person {
    position: absolute; right: 30px; top: 145px; text-align: right;
  }
  .person__name { font-weight: 600; font-size: 17px; color: var(--brown); line-height: 1.1; }
  .person__title { font-size: 12.5px; color: var(--orange); margin-top: 4px; line-height: 1; }
  .divider {
    position: absolute; left: 30px; top: 174px;
    width: 320px; height: 1px; background: var(--rule);
  }

  .contact {
    position: absolute; left: 30px; top: 191px;
    list-style: none; font-size: 11.5px; color: var(--ink);
  }
  .contact li { display: flex; align-items: center; gap: 6px; height: 17.5px; }
  .contact svg { width: 11px; height: 11px; fill: var(--brown); }

  .address {
    position: absolute; right: 30px; top: 191px;
    font-size: 11.5px; color: var(--ink); text-align: right; font-style: normal;
  }
  .address span { display: block; height: 17.5px; line-height: 17.5px; }
  .address .web { font-style: italic; color: var(--brown); }

  .back-brand {
    position: absolute; left: 0; right: 0; top: 110px;
    display: flex; justify-content: center; align-items: center; gap: 10px;
  }
  .back-brand__square { width: 14px; height: 14px; background: var(--orange); }
  .back-brand__name { font-weight: 600; font-size: 24px; color: var(--cream); }

  .services {
    position: absolute; left: 0; right: 0; top: 200px;
    text-align: center; font-style: italic; font-size: 12.5px;
    color: var(--cream); line-height: 18px;
  }
  .services .dot { color: var(--orange); font-style: normal; }
</style>
</head>
<body>
<main class="stage">
  <section class="card card--front" aria-label="Card front">
    <div class="brand-tab"></div>
    <div class="brand">
      <span class="brand__square"></span>
      <span class="brand__name">Meadowlark Property Review</span>
    </div>

    <div class="person">
      <p class="person__name">Daniel Harlow</p>
      <p class="person__title">CEO/Founder</p>
    </div>
    <div class="divider"></div>

    <ul class="contact">
      <li>
        <svg viewBox="0 0 24 24" aria-hidden="true"><path d="M6.6 10.8c1.4 2.8 3.8 5.1 6.6 6.6l2.2-2.2c.3-.3.7-.4 1-.2 1.1.4 2.3.6 3.6.6.6 0 1 .4 1 1V20c0 .6-.4 1-1 1C10.6 21 3 13.4 3 4c0-.6.4-1 1-1h3.5c.6 0 1 .4 1 1 0 1.3.2 2.5.6 3.6.1.3 0 .7-.2 1l-2.3 2.2z"/></svg>
        417 555 0182
      </li>
      <li>
        <svg viewBox="0 0 24 24" aria-hidden="true"><path d="M6 2h10l2 2v5H6zM3 10h18a1 1 0 0 1 1 1v7H2v-7a1 1 0 0 1 1-1zm3 10h12v2H6z"/></svg>
        417 555 0196
      </li>
      <li>
        <svg viewBox="0 0 24 24" aria-hidden="true"><path d="M2 5h20v14H2zm2 2v1l8 5 8-5V7l-8 5z"/></svg>
        office@meadowlarkpr.com
      </li>
    </ul>

    <address class="address">
      <span>2210 Larkspur Avenue</span>
      <span>Springfield, Missouri 65804</span>
      <span class="web">www.meadowlarkpr.com</span>
    </address>
  </section>

  <section class="card card--back" aria-label="Card back">
    <div class="back-brand">
      <span class="back-brand__square"></span>
      <span class="back-brand__name">Meadowlark Property Review</span>
    </div>
    <p class="services">
      Residential appraisals <span class="dot">•</span> Home inspection<br>
      Pest inspection and radon gas measurement.
    </p>
  </section>
</main>
</body>
</html>
```